Cool business cards

Use my existing logo from mark meadow (see images I have uploaded) and design a really cool non-stuffy business card. I am a divorce mediator.

```html
<!DOCTYPE html>
<html lang="en">
<head>
<meta charset="utf-8">
<title>Mark Meadow – Business Card</title>
<link rel="stylesheet" href="https://fonts.googleapis.com/css2?family=Roboto:wght@400;500&family=Saira+Semi+Condensed:wght@600&display=swap">
<style>
  :root {
    --backdrop: #bdbdbd;
    --teal: #2f9ea8;
    --green: #3a845f;
    --green-dark: #2f7a52;
    --paper: #f4f4f4;
    --ink: #2a2a2a;
    --white: #ffffff;
  }
  * { margin: 0; padding: 0; box-sizing: border-box; }
  html, body { width: 1200px; height: 576px; overflow: hidden; }
  body {
    background: var(--backdrop);
    font-family: "Roboto", Arial, sans-serif;
    position: relative;
  }
  .card {
    position: absolute;
    border-radius: 13px;
    overflow: hidden;
    box-shadow: 0 3px 8px rgba(0,0,0,0.25);
  }
  .card-front {
    left: 82px; top: 139px; width: 484px; height: 293px;
    background: linear-gradient(105deg, var(--teal) 0%, #349486 45%, var(--green) 100%);
    color: var(--white);
  }
  .card-back {
    left: 602px; top: 138px; width: 481px; height: 291px;
    background: var(--paper);
    color: var(--ink);
  }
  .brand {
    position: absolute;
    text-align: center;
    transform: translateX(-50%);
    white-space: nowrap;
  }
  .brand-name {
    font-family: "Roboto", Arial, sans-serif;
    font-weight: 400;
    letter-spacing: 1px;
  }
  .brand-tagline {
    display: flex;
    align-items: center;
    gap: 8px;
    justify-content: center;
    font-weight: 400;
    letter-spacing: 0.3px;
  }
  .brand-tagline .rule {
    height: 2px;
    background: currentColor;
    display: block;
  }
  .card-front .brand { left: 242px; top: 110px; }
  .card-front .brand-name { font-size: 34px; }
  .card-front .brand-tagline { font-size: 14px; margin-top: 14px; }
  .card-front .rule { width: 52px; }

  .card-back .brand { left: 157px; top: 82px; }
  .card-back .brand-name { font-size: 26px; color: var(--green-dark); }
  .card-back .brand-tagline { font-size: 11px; margin-top: 8px; color: var(--teal); }
  .card-back .rule { width: 44px; background: var(--green-dark); }

  .person {
    position: absolute;
    right: 24px; top: 36px;
    text-align: right;
  }
  .person-name {
    font-family: "Saira Semi Condensed", Arial, sans-serif;
    font-weight: 600;
    font-size: 20px;
    color: var(--green-dark);
    line-height: 1.1;
  }
  .person-role { font-size: 12.5px; margin-top: 4px; }
  .address { margin-top: 18px; font-size: 12.5px; line-height: 1.45; }

  .wave { position: absolute; left: 0; top: 0; width: 481px; height: 291px; }

  .contacts {
    position: absolute;
    right: 20px; top: 212px;
    list-style: none;
    color: var(--white);
    font-size: 12.5px;
  }
  .contacts li {
    display: flex; align-items: center; justify-content: flex-end;
    gap: 10px; height: 18.5px;
  }
  .contacts svg { width: 11px; height: 11px; fill: var(--white); }
</style>
</head>
<body>

<section class="card card-front">
  <div class="brand">
    <div class="brand-name">Mark Meadow</div>
    <div class="brand-tagline"><span class="rule"></span>I AM A DIVORCE MEDIATOR<span class="rule"></span></div>
  </div>
</section>

<section class="card card-back">
  <svg class="wave" viewBox="0 0 481 291" aria-hidden="true">
    <path d="M0,252 C110,318 240,262 330,205 C395,170 445,163 481,162 L481,291 L0,291 Z" fill="var(--green)"/>
    <path d="M0,222 C90,262 210,268 320,206 C390,168 440,150 481,148 L481,160 C440,162 395,178 330,216 C215,282 90,272 0,238 Z" fill="var(--teal)"/>
    <path d="M45,240 C140,272 230,262 290,232 C230,258 140,262 45,240 Z" fill="var(--teal)"/>
  </svg>

  <div class="brand">
    <div class="brand-name">Mark Meadow</div>
    <div class="brand-tagline"><span class="rule"></span>I AM A DIVORCE MEDIATOR<span class="rule"></span></div>
  </div>

  <div class="person">
    <div class="person-name">Ellen Brook</div>
    <div class="person-role">Managing Director</div>
    <div class="address">18 Willow Lane,<br>Fairview, US 10234</div>
  </div>

  <ul class="contacts">
    <li>555-010-2040
      <svg viewBox="0 0 12 12"><path d="M1,4 C1,2 3,1 6,1 C9,1 11,2 11,4 L8.5,4.5 L8,3.5 L4,3.5 L3.5,4.5 Z M3,5.5 L9,5.5 L10.5,10.5 L1.5,10.5 Z"/></svg></li>
    <li>ellen@meadowmediation.com
      <svg viewBox="0 0 12 12"><path d="M1,2.5 L11,2.5 L11,9.5 L1,9.5 Z M1.8,3.2 L6,6.5 L10.2,3.2 Z" fill-rule="evenodd"/></svg></li>
    <li>www.meadowmediation.com
      <svg viewBox="0 0 12 12"><circle cx="6" cy="6" r="5" fill="none" stroke="#fff" stroke-width="1"/><ellipse cx="6" cy="6" rx="2" ry="5" fill="none" stroke="#fff" stroke-width="0.9"/><path d="M1,6 L11,6" stroke="#fff" stroke-width="0.9"/></svg></li>
  </ul>
</section>

</body>
</html>
```